business card - for laser marking

I need design (curve) for my business card (make with laser) size 85mm x 55mm. How it look business card with laser marking see attached picture.

color:
Background: white
text and icons black

Please include: one side
1. dominik vrabec - direktor
2. phone: +386(0)41 726 190
+386(0)580 237 61
3. info@zarezko.example
4. faecebook.com/Zarezko.Ex
5. KM-ATELJE, Dominik Vrabec s.p.
Lipova ulica 19, 1000 Ljubljana, SI
6. logo

Please include: second side
1. logo
2. www.zarezko.example
3. Lasersko graviranje
ovitki telefonov, ohišja telefonov / tablic, nakit, ure, alu vizitke, dog-tagi, kemični svinčniki, orodja, noži, vžigalniki

Industry/Entity Type

Business

Contact Information for Business Card

Please include: one side
+386(0)580 237 61
3. info@zarezko.example
6. logo

1. logo
2. www.zarezko.example
3. Lasersko graviranje

Colors
000000
ffffff

Requirements
Must have
• I need design (curve) for my business card (make with laser) size 85mm x 55mm. How it look business card with laser marking see attached picture.
• color:
• Background: white
• text and icons black
• Please include: one side
• 1. dominik vrabec - direktor
• 2. phone: +386(0)41 726 190
• +386(0)580 237 61
• 3. info@zarezko.example
• 4. faecebook.com/Zarezko.Ex
• 5. KM-ATELJE, Dominik Vrabec s.p.
• Lipova ulica 19, 1000 Ljubljana, SI
• 6. logo
• Please include: second side
• 1. logo
• 2. www.zarezko.example
• 3. Lasersko graviranje
• ovitki telefonov, ohišja telefonov / tablic, nakit, ure, alu vizitke, dog-tagi, kemični svinčniki, orodja, noži, vžigalniki

```html
<!DOCTYPE html>
<html lang="sl">
<head>
<meta charset="utf-8">
<title>Zarezko – business card</title>
<link rel="stylesheet" href="https://fonts.googleapis.com/css2?family=Roboto:wght@400;500;700&display=swap">
<style>
  :root {
    --backdrop: #d9d9d9;
    --card-bg: #ffffff;
    --ink: #000000;
  }
  * { margin: 0; padding: 0; box-sizing: border-box; }
  html, body {
    width: 1200px;
    height: 960px;
    overflow: hidden;
  }
  body {
    position: relative;
    background: var(--backdrop);
    font-family: "Roboto", Arial, sans-serif;
    color: var(--ink);
  }
  .card {
    position: absolute;
    width: 614px;
    height: 343px;
    text-align: center;
    background: var(--card-bg);
    box-shadow: 0 2px 6px rgba(0,0,0,.2);
  }
  .card--front { left: 314px; top: 113px; }
  .card--back  { left: 311px; top: 472px; }

  .brand-mark {
    position: absolute;
    left: 0; right: 0;
    display: flex;
    align-items: center;
    justify-content: center;
    gap: 10px;
    font-weight: 700;
    letter-spacing: 1px;
    line-height: 1;
  }
  .brand-mark__dot {
    width: 14px; height: 14px;
    border-radius: 50%;
    background: var(--ink);
  }
  .card--front .brand-mark { top: 95px; font-size: 34px; }
  .card--back .brand-mark  { top: 134px; font-size: 28px; }

  .holder-name {
    position: absolute; left: 0; right: 0; top: 153px;
    font-size: 22px; font-weight: 700;
    text-transform: uppercase;
  }
  .holder-role {
    position: absolute; left: 0; right: 0; top: 180px;
    font-size: 15px; font-weight: 500;
    text-transform: uppercase;
  }
  .contact {
    position: absolute; left: 0; right: 0; top: 205px;
    font-size: 14px; line-height: 19px;
  }
  .services {
    position: absolute; left: 0; right: 0; top: 240px;
    font-size: 14px; line-height: 18.5px;
  }
  .website {
    position: absolute; left: 0; right: 0; top: 301px;
    font-size: 16px; font-weight: 500;
  }
</style>
</head>
<body>
  <section class="card card--front" aria-label="Front side">
    <div class="brand-mark"><span class="brand-mark__dot"></span>ZAREZKO</div>
    <h1 class="holder-name">Dominik Vrabec</h1>
    <p class="holder-role">Direktor</p>
    <p class="contact">
      KM-ATELJE, Dominik Vrabec s.p., Lipova ulica 19, 1000 Ljubljana, SI<br>
      P: +386(0)580 237 61 M: +386(0)41 726 190 E: info@zarezko.example<br>
      W: Zarezko.example F: faecebook.com/Zarezko.Ex
    </p>
  </section>

  <section class="card card--back" aria-label="Back side">
    <div class="brand-mark"><span class="brand-mark__dot"></span>ZAREZKO</div>
    <p class="services">
      Lasersko graviranje<br>
      ovitki telefonov, ohišja telefonov / tablic, nakit, ure, alu vizitke<br>
      dog-tagi, kemični svinčniki, orodja, noži, vžigalniki
    </p>
    <p class="website">www.zarezko.example</p>
  </section>
</body>
</html>
```